PPE EQIUPMENT

WE WOULD LIKE TO PRODUCE 2 DIFFERENT BANNERS TO BE PLACED OUTSIDE OF OUR WAREHOUSE TO ADVERTISE THAT WE HAVE FACE MASKS, HAND SANITISERS, DISINFECTANT SPRAY, FACE SHIELDS AND HAND SOAP. THE SIZE OF EACH BANNER WILL BE , portrait to be (W) 140 cm x (H) 250 cm, with 4 x eyelets. THE BANNER IS TO STATE PPE EQUIPMENT AVAILABLE HERE AND SHOW OUR PHONE NUMBER 0208-417-2953. FINALLY WE WILL REQUIRE SOME IMAGES OF THE PRODUCTS IF YOU CAN SUPPLY THESE. THANKS

```html
<!DOCTYPE html>
<html lang="en">
<head>
<meta charset="utf-8">
<title>PPE Equipment Banner</title>
<link rel="stylesheet" href="https://fonts.googleapis.com/css2?family=Oswald:wght@700&family=Roboto:wght@300&family=Rubik:wght@700&family=League+Spartan:wght@800&family=Barlow:wght@300;500&display=swap">
<style>
  :root {
    --navy: #1f3a70;
    --white: #ffffff;
    --backdrop: #d6d6d6;
    --eyelet-light: #828282;
    --eyelet-dark: #14213f;
    --icon-fill: #e2e7f0;
  }
  * { margin: 0; padding: 0; box-sizing: border-box; }
  html, body {
    width: 960px; height: 1200px; overflow: hidden;
    background: var(--backdrop);
  }
  .banner {
    position: absolute; left: 173px; top: 50px;
    width: 614px; height: 1100px;
    background: var(--white);
    color: var(--navy);
    overflow: hidden;
  }
  .eyelet {
    position: absolute; width: 32px; height: 32px;
    border-radius: 50%; border: 4px solid var(--eyelet-light);
    z-index: 2;
  }
  .eyelet.top-left { left: 12px; top: 11px; }
  .eyelet.top-right { right: 12px; top: 11px; }
  .eyelet.bottom-left { left: 12px; top: 1057px; border-color: var(--eyelet-dark); }
  .eyelet.bottom-right { right: 12px; top: 1057px; border-color: var(--eyelet-dark); }

  .headline {
    position: absolute; left: 0; right: 0; top: 54px;
    text-align: center;
    font-family: "Oswald", sans-serif; font-weight: 700;
    font-size: 84px; line-height: 1; letter-spacing: -1px;
  }
  .subhead {
    position: absolute; left: 0; right: 0; top: 156px;
    text-align: center;
    font-family: "Roboto", sans-serif; font-weight: 300;
    font-size: 48px; line-height: 1;
  }
  .phone-band {
    position: absolute; left: 0; right: 0; top: 215px; height: 107px;
    background: var(--navy); color: var(--white);
    display: flex; align-items: center; justify-content: center;
    font-family: "Rubik", sans-serif; font-weight: 700;
    font-size: 64px; letter-spacing: 0.5px;
  }
  .product-icon {
    position: absolute; width: 143px; height: 111px;
    border: 9px solid var(--navy); border-radius: 11px;
    padding: 4px;
  }
  .product-icon .art {
    width: 100%; height: 100%; background: var(--icon-fill); border-radius: 3px;
  }
  .icon-mask { left: 44px; top: 353px; }
  .icon-sanitiser { left: 226px; top: 353px; }
  .icon-spray { left: 407px; top: 353px; }
  .icon-shield { left: 132px; top: 497px; }
  .icon-soap { left: 321px; top: 497px; }

  .product-list {
    position: absolute; left: 0; right: 0; top: 638px;
    list-style: none; text-align: center;
    font-family: "League Spartan", sans-serif; font-weight: 800;
    font-size: 50px; line-height: 55px; letter-spacing: -0.5px;
  }
  .footer-band {
    position: absolute; left: 0; right: 0; top: 939px; height: 161px;
    background: var(--navy); color: var(--white);
    text-align: center;
  }
  .company-name {
    position: absolute; left: 0; right: 0; top: 24px;
    font-family: "Barlow", sans-serif; font-weight: 500;
    font-size: 54px; line-height: 1; letter-spacing: 1px;
  }
  .company-tagline {
    position: absolute; left: 0; right: 0; top: 86px;
    font-family: "Barlow", sans-serif; font-weight: 300;
    font-size: 28px; line-height: 1; letter-spacing: 1px;
  }
</style>
</head>
<body>
  <main class="banner">
    <span class="eyelet top-left"></span>
    <span class="eyelet top-right"></span>

    <h1 class="headline">PPE EQUIPMENT</h1>
    <p class="subhead">AVAILABLE HERE</p>

    <div class="phone-band">0208-417-2953</div>

    <div class="product-icon icon-mask"><div class="art" role="img" aria-label="Face mask pictogram"></div></div>
    <div class="product-icon icon-sanitiser"><div class="art" role="img" aria-label="Hands under hand sanitiser pump bottle pictogram"></div></div>
    <div class="product-icon icon-spray"><div class="art" role="img" aria-label="Disinfectant spray bottle pictogram"></div></div>
    <div class="product-icon icon-shield"><div class="art" role="img" aria-label="Face shield pictogram"></div></div>
    <div class="product-icon icon-soap"><div class="art" role="img" aria-label="Hand holding a bar of soap pictogram"></div></div>

    <ul class="product-list">
      <li>FACE MASKS</li>
      <li>HAND SANITISERS</li>
      <li>DISINFECTANT SPRAY</li>
      <li>FACE SHIELDS</li>
      <li>HAND SOAP</li>
    </ul>

    <footer class="footer-band">
      <p class="company-name">HALDEN TRADE SUPPLY</p>
      <p class="company-tagline">WAREHOUSE COLLECTION &amp; DELIVERY</p>
    </footer>

    <span class="eyelet bottom-left"></span>
    <span class="eyelet bottom-right"></span>
  </main>
</body>
</html>
```